Copperbend Blazeworks Website Design

I am looking for a website design ( Home page and inner template page ) in a .psd format. The home page needs to have a large hero image what will function as a "slider", and have some highlight graphical areas/links to the following links "Public & Municipal Events", "Corporate Events", "Special Events". The main navigation needs to have the following nav links "gallery", "home", "about", "services" and "contact". Unfortunately the client does not have any nice hi-rez images ( this is a company that specializes is large fireworks displays ) so please use stock photography sample images from snapvaultpics since we have an account there an can purchase the photos if our client wants to use them. Our current full time graphic artist has been with us for a long time so we are looking at artflockhub as a way to add a fresh approach to design and possibly find someone we can work with regularly. Here is a few designs that in the way we display them for our clients for approval. As you can see there are a couple that don't have their own images so they are utilizing the before mentioned snapvaultpics samples. On the plus side we did manage to get their logo in a .ai format. We have our team for handling the conversion from design to html.

http://reedfoxbuildstudio.com/dev/

```html
<!DOCTYPE html>
<html lang="en">
<head>
<meta charset="utf-8">
<title>Copperbend Blazeworks</title>
<link href="https://fonts.googleapis.com/css2?family=Merriweather:wght@400;700;900&family=Lato:wght@400;700;900&family=Dancing+Script:wght@400&display=swap" rel="stylesheet">
<style>
:root{
  --blue:#3b8fd0;
  --footer-blue:#3e97d9;
  --navy:#0b1530;
  --ink:#111418;
  --text:#333a40;
  --line:#d6d9dc;
  --white:#ffffff;
}
*{margin:0;padding:0;box-sizing:border-box}
html,body{width:1200px;height:3523px;overflow:hidden;background:var(--white)}
body{position:relative;font-family:'Lato',sans-serif;color:var(--text)}
.abs{position:absolute}

/* header */
.site-header{position:absolute;left:0;top:0;width:1200px;height:126px;background:var(--white)}
.header-rule{position:absolute;top:71px;height:1px;background:var(--line)}
.call{position:absolute;left:144px;top:17px;display:flex;align-items:center;gap:12px}
.call-icon{width:36px;height:36px;border-radius:50%;background:var(--blue);display:flex;align-items:center;justify-content:center}
.call small{display:block;font-family:'Merriweather',serif;font-weight:700;font-size:12px;color:var(--ink)}
.call strong{display:block;font-family:'Merriweather',serif;font-weight:700;font-size:17px;color:var(--ink);line-height:1.1}
.join{position:absolute;left:865px;top:15px;width:145px;height:41px;border:2px solid var(--blue);border-radius:22px;color:var(--blue);font-family:'Merriweather',serif;font-weight:700;font-size:15px;display:flex;align-items:center;justify-content:center}
.search{position:absolute;left:1030px;top:22px}
.nav a{position:absolute;top:84px;font-family:'Merriweather',serif;font-size:17px;color:var(--ink);text-decoration:none}
.nav a.active{color:var(--blue)}
.header-band{position:absolute;left:0;top:120px;width:1200px;height:6px;background:var(--ink)}
.logo-tab{position:absolute;left:470px;top:0;width:260px;height:148px;z-index:3}
.brand{position:absolute;text-align:center;font-family:'Merriweather',serif;font-weight:400;color:var(--navy);line-height:1.15}
.brand-dot{position:absolute;border-radius:50%;background:var(--blue)}

/* hero */
.hero{position:absolute;left:0;top:126px;width:1200px;height:722px;background:radial-gradient(ellipse at 25% 30%,#3a2a5a 0%,transparent 40%),radial-gradient(ellipse at 80% 35%,#2c4a3a 0%,transparent 40%),linear-gradient(180deg,#0d1a3a 0%,#1b2b55 50%,#0b1430 100%)}
.hero-script{position:absolute;left:0;width:1200px;top:440px;text-align:center;font-family:'Dancing Script',cursive;font-size:56px;color:var(--white)}
.hero-title{position:absolute;left:0;width:1200px;top:505px;text-align:center;font-family:'Merriweather',serif;font-weight:900;font-size:58px;line-height:62px;color:var(--white)}
.btn{position:absolute;background:var(--blue);color:var(--white);font-family:'Lato',sans-serif;font-weight:700;letter-spacing:.5px;display:flex;align-items:center;justify-content:center;border-radius:3px}
.dots{position:absolute;left:568px;top:770px;display:flex;gap:8px;z-index:2}
.dots span{width:16px;height:16px;border-radius:50%;border:2px solid var(--white)}
.dots span.on{background:var(--blue);border-color:var(--blue)}
.hero-edge{position:absolute;left:0;top:740px;z-index:1}

/* section headings */
.kicker{position:absolute;left:0;width:1200px;text-align:center;font-family:'Dancing Script',cursive;font-size:20px;color:var(--ink)}
.section-title{position:absolute;left:0;width:1200px;text-align:center;font-family:'Merriweather',serif;font-weight:700;font-size:38px;color:var(--ink)}
.title-rule{position:absolute;left:564px;width:72px;height:3px;background:#555b60}

/* services */
.service-card{position:absolute;top:1029px;width:285px;height:474px;background:var(--white);border:1px solid #e2e4e6;box-shadow:0 1px 4px rgba(0,0,0,.08);text-align:center}
.service-media{width:283px;height:243px;clip-path:polygon(0 0,100% 0,100% 89%,50% 100%,0 89%)}
.service-card h3{margin-top:36px;font-family:'Merriweather',serif;font-weight:700;font-size:18px;color:var(--ink)}
.service-card p{margin:12px auto 0;width:250px;font-size:15px;line-height:21px;color:var(--text)}
.outline-btn{display:flex;margin:18px auto 0;width:144px;height:40px;border:2px solid var(--blue);border-radius:22px;align-items:center;justify-content:center;font-size:12px;font-weight:700;color:var(--blue);letter-spacing:.5px}

/* welcome */
.welcome{position:absolute;left:0;top:1599px;width:1200px;height:558px;background:radial-gradient(ellipse at 22% 45%,#7a1f3a 0%,#3a1230 22%,transparent 45%),linear-gradient(180deg,#0a0f22 0%,#121a30 70%,#2a1028 100%)}
.welcome-script{position:absolute;left:642px;top:70px;font-family:'Dancing Script',cursive;font-size:38px;color:var(--white)}
.welcome-title{position:absolute;left:642px;top:110px;font-family:'Merriweather',serif;font-weight:700;font-size:38px;color:var(--white)}
.welcome-rule{position:absolute;left:642px;top:175px;width:88px;height:3px;background:var(--white)}
.welcome-copy{position:absolute;left:642px;top:202px;width:470px;font-size:16px;line-height:25px;color:#e6e9ef}

/* gallery */
.tile{position:absolute}
.arrow{position:absolute;width:38px;height:38px;border-radius:50%;background:var(--white);display:flex;align-items:center;justify-content:center;z-index:2}

/* footer */
.site-footer{position:absolute;left:0;top:3034px;width:1200px;height:489px;background:var(--footer-blue);color:var(--white)}
.foot-h{position:absolute;font-family:'Lato',sans-serif;font-weight:700;font-size:19px;color:var(--white)}
.contact-item{position:absolute;left:144px;display:flex;gap:22px;align-items:flex-start;font-size:15px;line-height:21px}
.ring{flex:none;width:36px;height:36px;border-radius:50%;border:2px solid var(--white);display:flex;align-items:center;justify-content:center}
.v-rule{position:absolute;top:3108px;width:1px;height:228px;background:rgba(255,255,255,.6)}
.social{position:absolute;top:3289px;left:458px;display:flex;gap:12px}
.social span{width:34px;height:34px;border-radius:50%;border:2px solid var(--white)}
.newsletter-copy{position:absolute;left:721px;top:3166px;width:340px;font-size:15px;line-height:24px}
.subscribe{position:absolute;left:721px;top:3231px;width:334px;height:48px;border:2px solid var(--white);border-radius:26px}
.subscribe span{position:absolute;left:18px;top:13px;font-size:14px}
.subscribe b{position:absolute;right:4px;top:4px;width:130px;height:36px;border-radius:20px;background:#0d1218;font-size:12px;display:flex;align-items:center;justify-content:center;letter-spacing:.5px}
.foot-rule{position:absolute;left:144px;top:3404px;width:912px;height:1px;background:rgba(255,255,255,.5)}
.copyright{position:absolute;left:0;width:1200px;top:3453px;text-align:center;font-size:15px}
</style>
</head>
<body>

<header class="site-header">
  <div class="header-rule" style="left:0;width:450px"></div>
  <div class="header-rule" style="left:750px;width:450px"></div>
  <div class="call">
    <div class="call-icon">
      <svg width="18" height="18" viewBox="0 0 24 24"><path fill="#fff" d="M6.6 10.8a15 15 0 0 0 6.6 6.6l2.2-2.2c.3-.3.7-.4 1-.2 1.1.4 2.3.6 3.6.6.6 0 1 .4 1 1V20c0 .6-.4 1-1 1A17 17 0 0 1 3 4c0-.6.4-1 1-1h3.5c.6 0 1 .4 1 1 0 1.3.2 2.5.6 3.6.1.3 0 .7-.2 1z"/></svg>
    </div>
    <div><small>Call Us</small><strong>555 0142 7700</strong></div>
  </div>
  <div class="join">Join Now</div>
  <svg class="search" width="28" height="28" viewBox="0 0 24 24"><circle cx="10" cy="10" r="7" fill="none" stroke="#9aa0a6" stroke-width="3"/><path d="M15 15l6 6" stroke="#9aa0a6" stroke-width="3.4" stroke-linecap="round"/></svg>
  <nav class="nav">
    <a class="active" style="left:144px">Home</a>
    <a style="left:240px">About</a>
    <a style="left:336px">Services</a>
    <a style="left:743px">Our Gallery</a>
    <a style="left:892px">Contact Us</a>
  </nav>
  <div class="header-band"></div>
</header>

<div class="logo-tab">
  <svg width="260" height="148" viewBox="0 0 260 148"><path d="M10 120 Q130 160 250 120 L250 0 L10 0 Z" fill="#fff"/></svg>
  <span class="brand-dot" style="left:121px;top:30px;width:18px;height:18px"></span>
  <div class="brand" style="left:0;top:60px;width:260px;font-size:22px">Copperbend<br>Blazeworks</div>
</div>

<section class="hero" role="img" aria-label="Night harbour skyline with colourful fireworks bursting over the water"></section>
<div class="hero-script">Copperbend Blazeworks</div>
<div class="hero-title">Public and<br>Municipal Events</div>
<div class="btn" style="left:512px;top:651px;width:176px;height:49px;font-size:16px">LEARN MORE</div>
<div class="dots"><span class="on"></span><span></span><span></span></div>
<svg class="hero-edge" width="1200" height="112" viewBox="0 0 1200 112">
  <path d="M0 22 Q600 112 1200 22 L1200 112 L0 112 Z" fill="#fff"/>
  <path d="M100 44 Q600 120 1100 44 Q600 96 100 44 Z" fill="#3b8fd0"/>
</svg>

<div class="kicker" style="top:895px">Copperbend Blazeworks</div>
<h2 class="section-title" style="top:922px">Our Services</h2>
<div class="title-rule" style="top:987px"></div>

<article class="service-card" style="left:144px">
  <div class="service-media" role="img" aria-label="Fireworks over a waterfront city at night" style="background:linear-gradient(160deg,#3a1440 0%,#7a2c6a 45%,#1a1a3a 100%)"></div>
  <h3>Public &amp; Municipal Events</h3>
  <p>Sed ut perspiciatis unde omnis iste natus voluptatem accusantium doemque laudantium, totam rem aperiam, eaque ipsa quae</p>
  <span class="outline-btn">LEARN MORE</span>
</article>
<article class="service-card" style="left:458px">
  <div class="service-media" role="img" aria-label="Crowd silhouettes watching fireworks above city lights" style="background:linear-gradient(170deg,#2a1a2a 0%,#6a3a3a 40%,#1a2a4a 75%,#050508 100%)"></div>
  <h3>Corporate Events</h3>
  <p>Sed ut perspiciatis unde omnis iste natus voluptatem accusantium doemque laudantium, totam rem aperiam, eaque ipsa quae</p>
  <span class="outline-btn">LEARN MORE</span>
</article>
<article class="service-card" style="left:772px">
  <div class="service-media" role="img" aria-label="Festival audience with raised hands under bright fireworks" style="background:linear-gradient(160deg,#4a3a20 0%,#8a4a7a 45%,#2a1a3a 100%)"></div>
  <h3>Special Events</h3>
  <p>Sed ut perspiciatis unde omnis iste natus voluptatem accusantium doemque laudantium, totam rem aperiam, eaque ipsa quae</p>
  <span class="outline-btn">LEARN MORE</span>
</article>

<section class="welcome" role="img" aria-label="Large red firework over a harbour skyline at night">
  <div class="welcome-script">Welcome to</div>
  <h2 class="welcome-title">Copperbend Blazeworks</h2>
  <div class="welcome-rule"></div>
  <p class="welcome-copy">Sed ut perspiciatis unde omnis iste natus error sit voluptatem accusantium doloremque laudantium, totam rem aperiam, eaque ipsa quae ab illo inventore veritatis et quasi architecto beatae vitae dicta sunt explicabo. Nemo enim ipsam volatem quia voluptas sit asrnatur aut odit aut fugit, sed quia conuntur magni dolores eos qui ratione voluptatem sequi nesciunt.</p>
  <div class="btn" style="left:642px;top:376px;width:162px;height:44px;font-size:15px">LEARN MORE</div>
</section>

<div class="kicker" style="top:2218px">Copperbend Blazeworks</div>
<h2 class="section-title" style="top:2245px">Our Gallery</h2>
<div class="title-rule" style="top:2307px"></div>

<div class="tile" style="left:0;top:2357px;width:387px;height:331px;background:linear-gradient(170deg,#0a0a12 0%,#6a1a4a 45%,#1a0a10 100%)" role="img" aria-label="Pink and red fireworks reflected on water"></div>
<div class="tile" style="left:397px;top:2357px;width:387px;height:331px;background:linear-gradient(180deg,#0a0a14 0%,#3a2a2a 45%,#5a4a2a 70%,#0a0a14 100%)" role="img" aria-label="Fireworks above a lit riverside palace and clock tower"></div>
<div class="tile" style="left:795px;top:2357px;width:405px;height:331px;background:linear-gradient(170deg,#1a2a6a 0%,#6a2a6a 40%,#1a3a8a 70%,#050a20 100%)" role="img" aria-label="Concert crowd under blue and red fireworks"></div>
<div class="tile" style="left:0;top:2698px;width:387px;height:328px;background:linear-gradient(170deg,#1a1a3a 0%,#8a3a1a 55%,#c85a1a 80%,#2a0a0a 100%)" role="img" aria-label="People around a bonfire under fireworks"></div>
<div class="tile" style="left:397px;top:2698px;width:387px;height:328px;background:linear-gradient(170deg,#2a1a10 0%,#7a3a1a 40%,#1a1020 75%,#3a2a10 100%)" role="img" aria-label="Gold fireworks over a city at night"></div>
<div class="tile" style="left:795px;top:2698px;width:405px;height:328px;background:linear-gradient(170deg,#1a1a3a 0%,#5a3a7a 45%,#2a1a4a 75%,#0a0a20 100%)" role="img" aria-label="Purple fireworks above a monument skyline"></div>
<div class="arrow" style="left:104px;top:2669px"><svg width="20" height="20" viewBox="0 0 24 24"><path d="M20 12H5M11 5l-7 7 7 7" fill="none" stroke="#111" stroke-width="3" stroke-linecap="round" stroke-linejoin="round"/></svg></div>
<div class="arrow" style="left:1056px;top:2669px"><svg width="20" height="20" viewBox="0 0 24 24"><path d="M4 12h15M13 5l7 7-7 7" fill="none" stroke="#111" stroke-width="3" stroke-linecap="round" stroke-linejoin="round"/></svg></div>

<footer class="site-footer"></footer>
<div class="foot-h" style="left:144px;top:3106px">CONTACT US</div>
<div class="contact-item" style="top:3160px">
  <span class="ring"><svg width="16" height="16" viewBox="0 0 24 24"><path fill="#fff" d="M12 2a7 7 0 0 0-7 7c0 5 7 13 7 13s7-8 7-13a7 7 0 0 0-7-7zm0 9.5A2.5 2.5 0 1 1 12 6.5a2.5 2.5 0 0 1 0 5z"/></svg></span>
  <span>Copperbend Blazeworks<br>429 enim ipsam vtatem<br>quia voluptas sit</span>
</div>
<div class="contact-item" style="top:3238px">
  <span class="ring"><svg width="16" height="16" viewBox="0 0 24 24"><path fill="#fff" d="M6.6 10.8a15 15 0 0 0 6.6 6.6l2.2-2.2c.3-.3.7-.4 1-.2 1.1.4 2.3.6 3.6.6.6 0 1 .4 1 1V20c0 .6-.4 1-1 1A17 17 0 0 1 3 4c0-.6.4-1 1-1h3.5c.6 0 1 .4 1 1 0 1.3.2 2.5.6 3.6.1.3 0 .7-.2 1z"/></svg></span>
  <span>Phone:<br>555 0198 3300</span>
</div>
<div class="contact-item" style="top:3290px">
  <span class="ring"><svg width="16" height="16" viewBox="0 0 24 24"><path fill="#fff" d="M3 6h18v12H3z"/><path d="M3 6l9 7 9-7" fill="none" stroke="#3e97d9" stroke-width="2"/></svg></span>
  <span>Email:<br>hello@copperbendblaze.com</span>
</div>
<div class="v-rule" style="left:410px"></div>
<div class="v-rule" style="left:683px"></div>
<span class="brand-dot" style="left:537px;top:3136px;width:18px;height:18px;background:#fff"></span>
<div class="brand" style="left:420px;top:3172px;width:253px;font-size:24px;color:#fff">Copperbend<br>Blazeworks</div>
<div class="social" aria-label="Social links"><span></span><span></span><span></span><span></span></div>
<div class="foot-h" style="left:721px;top:3106px">SIGN UP FOR NEWSLETTER</div>
<p class="newsletter-copy">Excepteur sint occaecat cupidatat non proident, sunt in culpa qui Nemo enim ipsam</p>
<div class="subscribe"><span>Enter Email</span><b>SUBSCRIBE</b></div>
<div class="foot-rule"></div>
<div class="copyright">Copperbend Blazeworks © 2021 All Rights Reserved | Privacy Policy</div>

</body>
</html>
```